London Whisky Bottle Label

BACKGROUND
We are plumbers that have resurrected London's oldest once illicit Gin Distillery Harlow Post Wire https://www.vidtrove-example.net/clip/kq83pz
Bought 150yr old derelict bakery & turned it into an office for our plumbing biz....removed dangerous chimney...got sued by a neighbour ..
our lawyers discovered that the original bakers family once made illict gin here (in what is now our office) we tracked down the origianl family ...see pic enclosed....the little boy now in his 90's (Colin Treadle) gave us his family's secret gin recipe and we have now resurrected it. We supply Ravensmoor Hall, Hse of Wardens Pelling Drue etc. Now have our 1st London Whisky.
This is NOT scotch whisky...this a brand new category of drink 'English Whisky'
1. traditional whisky style bottle which will have embossed text on as per the sample English Whisky & K T Distillery LONDON
Front label 110mm x 95mm
Rear label 70mm wide and 100mm
Front Text TBC
Rear Text TBC
Must have a old map of my area London Q7 2XZ on rear
Map link https://charts.oldsheet-example.org/view/558210#zoom=6

Target Market(s)

OVER 30's

Font styles to use
Sans Serif

Requirements
Nice to have
• I want an old map on the front of the label....the map have 2 small rivers on it which are very close to my distillery (called The Hollin Race and Catter Beck, where they meet there a small bridge called Gravewick Bridge, i would like this shown on the map, is there any tasteful way to add some colour to the historic map ???

```html
<!DOCTYPE html>
<html lang="en">
<head>
<meta charset="utf-8">
<title>Wenlow English Whisky – Label Set</title>
<link href="https://fonts.googleapis.com/css2?family=Cormorant+Garamond:wght@400;500;600&display=swap" rel="stylesheet">
<style>
  :root {
    --canvas: #ffffff;
    --label-red: #7a1c19;
    --label-red-deep: #6b1512;
    --gold: #d8b25a;
    --gold-light: #f0d58c;
    --cream: #ece3d2;
    --map-paper: #e9e4d2;
    --map-ink: #bdb59c;
  }
  * { box-sizing: border-box; margin: 0; padding: 0; }
  html, body {
    width: 1200px; height: 1200px; overflow: hidden;
    background: var(--canvas);
    font-family: "Cormorant Garamond", Georgia, serif;
  }
  .canvas {
    position: relative; width: 1200px; height: 1200px;
    display: flex; align-items: center; justify-content: center; gap: 90px;
  }
  .label { position: relative; color: var(--cream); }
  .label-frame { position: absolute; inset: 0; width: 100%; height: 100%; }

  /* Front label */
  .front-label {
    width: 540px; height: 450px;
    background: linear-gradient(180deg, var(--label-red) 0%, var(--label-red-deep) 100%);
    display: flex; flex-direction: column; align-items: center; justify-content: center;
  }
  .front-label .brand-name {
    position: relative;
    font-weight: 600; font-size: 96px; line-height: 1;
    color: var(--cream); letter-spacing: 2px;
  }
  .front-label .category {
    position: relative;
    margin-top: 26px;
    font-weight: 400; font-size: 46px; letter-spacing: 1px;
    color: var(--cream);
  }
  .front-label .distillery {
    position: relative;
    margin-top: 18px;
    font-size: 17px; letter-spacing: 4px; text-transform: uppercase;
    color: #d9c3b3;
  }

  /* Rear label */
  .rear-label {
    width: 380px; height: 540px;
    background: var(--label-red);
    display: flex; flex-direction: column; align-items: center;
    padding: 30px 36px 0;
  }
  .rear-label .brand-name {
    position: relative;
    font-weight: 600; font-size: 58px; line-height: 1;
    color: var(--gold);
  }
  .rear-label .intro {
    position: relative;
    margin-top: 28px;
    font-size: 12.5px; line-height: 1.4; text-align: center; color: var(--cream);
  }
  .rear-label .map-area {
    position: relative;
    margin-top: 14px; width: 340px; height: 232px;
    background: radial-gradient(ellipse at 50% 45%, var(--map-paper) 0%, #ddd6c0 100%);
    border: 1px solid var(--map-ink);
  }
  .rear-label .volume {
    position: relative;
    margin-top: 20px; font-size: 13px; color: var(--cream);
  }
  .rear-label .footnote {
    position: relative;
    margin-top: 6px; width: 150px;
    font-size: 12px; line-height: 1.35; text-align: center; color: var(--cream);
  }
</style>
</head>
<body>
<main class="canvas">

  <section class="label front-label" aria-label="Front label">
    <svg class="label-frame" viewBox="0 0 540 450" preserveAspectRatio="none" aria-hidden="true">
      <line x1="0" y1="3" x2="540" y2="3" stroke="#d8b25a" stroke-width="4"/>
      <line x1="0" y1="447" x2="540" y2="447" stroke="#d8b25a" stroke-width="4"/>
      <path d="M34 26 H506 A14 14 0 0 0 520 40 V410 A14 14 0 0 0 506 424 H34 A14 14 0 0 0 20 410 V40 A14 14 0 0 0 34 26 Z"
            fill="none" stroke="#d8b25a" stroke-width="3"/>
    </svg>
    <div class="brand-name">Wenlow</div>
    <div class="category">ENGLISH WHISKY</div>
    <div class="distillery">K T Distillery London</div>
  </section>

  <section class="label rear-label" aria-label="Rear label">
    <svg class="label-frame" viewBox="0 0 380 540" preserveAspectRatio="none" aria-hidden="true">
      <path d="M16 2 H364 A14 14 0 0 0 378 16 V524 A14 14 0 0 0 364 538 H16 A14 14 0 0 0 2 524 V16 A14 14 0 0 0 16 2 Z"
            fill="none" stroke="#d8b25a" stroke-width="3"/>
    </svg>
    <div class="brand-name">Wenlow</div>
    <p class="intro">Lorem ipsum dolor sit amet, consectetuer adipiscing elit, sed diam nonummy nibh euismod tincidunt ut laoreet dolore magna aliquam erat volutpat. Ut wisi enim ad minim veniam, quis</p>
    <div class="map-area" role="img" aria-label="Historic map of the distillery area around Q7 2XZ, showing The Hollin Race, Catter Beck and Gravewick Bridge"></div>
    <p class="volume">800 ML</p>
    <p class="footnote">Lorem ipsum dolor sit amet, consectetuer adipiscing elit, sed diam nonummy nibh euismod</p>
  </section>

</main>
</body>
</html>
```